BUSINESS CARD - HALLORAN FIELD SERVICES

I would like to create a business card for my fertilizer spreading business. I would like to incorporate my existing logo and also a description of the services offered. The business card will be given to farmers so must be kept simple but effective. It will also be left in stores so much also be eye catching in order to stand out from other cards.

Target Market(s)

FARMERS

Requirements
Must have
• FRONT OF CARD = EXISTING LOGO + "CUSTOMISED SPREADING" below the logo

REAR Of CARD = SERVICES OFFERED AND CONTACT DETAILS

- Bulk fertilizer including Lime, Gypsum, Manure & Compost
- Granular fertilizer including Single Super, Urea, Gran-am, & Custom Blends
- Modern equipment - Autosteer & Variable Rate Capable
- Friendly & Reliable Service
- Contact Gus: 0417 552 308
Nice to have
• utilize same color scheme as existing logo

```html
<!DOCTYPE html>
<html lang="en">
<head>
<meta charset="utf-8">
<title>Halloran Field Services – Business Card</title>
<link href="https://fonts.googleapis.com/css2?family=Arimo:wght@400;700&display=swap" rel="stylesheet">
<style>
  :root {
    --backdrop: #222120;
    --orange: #f6961f;
    --white: #ffffff;
    --slate: #58585a;
    --shadow: rgba(0, 0, 0, 0.55);
  }
  * { margin: 0; padding: 0; box-sizing: border-box; }
  html, body {
    width: 1065px;
    height: 1200px;
    overflow: hidden;
    background: var(--backdrop);
    font-family: "Arimo", Arial, sans-serif;
  }
  .canvas { position: relative; width: 1065px; height: 1200px; }

  .card {
    position: absolute;
    width: 583px;
    height: 362px;
    box-shadow: 3px 4px 3px var(--shadow);
  }

  /* Rear: services and contact */
  .card-rear {
    left: 292px;
    top: 218px;
    background: var(--orange);
    border-radius: 0 181px 181px 0;
    color: var(--white);
  }
  .service-list { list-style: none; position: absolute; left: 25px; top: 46px; }
  .service {
    position: relative;
    padding-left: 16px;
    font-size: 16.6px;
    line-height: 19.8px;
    margin-bottom: 6.5px;
  }
  .service::before {
    content: "";
    position: absolute;
    left: 0;
    top: 4.5px;
    width: 11px;
    height: 11px;
    border-radius: 50%;
    background: var(--white);
  }
  .contact {
    position: absolute;
    left: 28px;
    top: 284px;
    font-size: 24.5px;
    line-height: 30px;
  }
  .rear-mark {
    position: absolute;
    left: 362px;
    top: 102px;
    width: 160px;
    height: 160px;
    border-radius: 50%;
    background: var(--white);
  }

  /* Front: brand and tagline */
  .card-front {
    left: 263px;
    top: 623px;
    background: var(--white);
    border-radius: 181px 0 0 181px;
  }
  .brand-mark {
    position: absolute;
    left: 211px;
    top: 58px;
    width: 150px;
    height: 150px;
    border-radius: 50%;
    background: var(--slate);
  }
  .brand-name {
    position: absolute;
    left: 0;
    width: 100%;
    top: 226px;
    text-align: center;
    color: var(--slate);
    font-weight: 700;
    font-size: 27px;
    letter-spacing: 1px;
  }
  .tagline {
    position: absolute;
    left: 0;
    width: 100%;
    top: 298px;
    text-align: center;
    color: var(--orange);
    font-size: 20px;
    letter-spacing: 1.6px;
  }
</style>
</head>
<body>
<main class="canvas">
  <section class="card card-rear" aria-label="Back of card">
    <ul class="service-list">
      <li class="service">Bulk fertilizer including Lime<br>Gypsum, Manure &amp; Compost</li>
      <li class="service">Granular fertilizer including<br>Single Super, Urea<br>Gran-am, &amp; Custom Blends</li>
      <li class="service">Modern equipment</li>
      <li class="service">Autosteer &amp; Variable Rate Capable</li>
      <li class="service">Friendly &amp; Reliable Service</li>
    </ul>
    <p class="contact">Contact Gus: 0417 552 308</p>
    <div class="rear-mark" aria-hidden="true"></div>
  </section>

  <section class="card card-front" aria-label="Front of card">
    <div class="brand-mark" aria-hidden="true"></div>
    <h1 class="brand-name">HALLORAN FIELD SERVICES</h1>
    <p class="tagline">CUSTOMISED SPREADING</p>
  </section>
</main>
</body>
</html>
```